Business Cards for new orthopaedic surgery practice

My husband and I are starting our own orthopaedic surgery practice. We are looking for a business card that is uniform, but one will have my name/title and the other will have his. You can just create one design with my name on it for now. But when I choose your design as the winning design I will ask that you add another copy with his name/title.

We are looking for classy, simple, elite all in one. We like dark blues/a little gold/yellow. Something that goes with our logo. We want our logo incorporated. Here is all the info you need:
Business name: RV Bone & Vitality Center
Location: 38517 North Willowmere Ave
Palm Verde, FL 33094
Phone: 954-218-4063
Fax: 954-582-7341
Email: info@myrvbonecare.example

Names: Lydia Vance, M.D.
Board Certified Hand and Upper Extremity Surgeon

Ebo Dansu, M.D.
Board Certified Hip & Knee Replacement/General Orthopaedic Surgeon

Can decide what you want to put on the back. Maybe a slogan:
Grounded in Care. Built for You

I am just going to upload our logo. The only thing is if we select you as the winning design, the location, and phone numbers may change. We will need your help to update that once fully solidified.

Industry/Entity Type

Medical

Contact Information for Business Card

Colors
0054AA
0677BA
7BADD7
CADEEF
E8F1F8
0094D4
00A9DD
6FCCEA
C7EBF8
E9F6FB

Requirements
Must have
• class, appeal,
Should not have
• We want to air on the side of masculine if we are looking at masculine vs. feminine feel. But we still want it classy, sophisticated, and something we will love

```html
<!DOCTYPE html>
<html lang="en">
<head>
<meta charset="utf-8">
<title>RV Bone &amp; Vitality Center — Business Card</title>
<link rel="stylesheet" href="https://fonts.googleapis.com/css2?family=Montserrat:wght@400;500;600;700&display=swap">
<style>
  :root {
    --navy: #1a2a56;
    --navy-deep: #1b2b58;
    --gold: #c9a45c;
    --ink: #1d2233;
    --paper: #ffffff;
    --backdrop: #e6e6e8;
  }
  * { margin: 0; padding: 0; box-sizing: border-box; }
  html, body {
    width: 1200px; height: 1108px; overflow: hidden;
    background: var(--backdrop);
    font-family: "Montserrat", sans-serif;
  }
  .canvas { position: relative; width: 1200px; height: 1108px; }

  .card { position: absolute; }
  .card-front { left: 219px; top: 50px; width: 775px; height: 473px; background: var(--paper); }
  .card-back { left: 217px; top: 568px; width: 777px; height: 456px; background: var(--navy-deep); }

  .brand-mark {
    position: absolute; left: 117px; top: 190px; width: 240px;
    text-align: center; color: var(--navy);
    font-weight: 600; font-size: 24px; line-height: 1.3; letter-spacing: 0.02em;
  }

  .divider {
    position: absolute; left: 368px; top: 127px; width: 2px; height: 232px;
    background: var(--navy);
  }

  .details { position: absolute; left: 387px; top: 124px; color: var(--ink); }
  .doctor-name { font-size: 28px; font-weight: 600; color: var(--navy); line-height: 1.2; }
  .doctor-name .credential { color: var(--gold); }
  .doctor-title { font-size: 17.5px; line-height: 1.3; margin-top: 4px; }
  .address { font-size: 17.5px; line-height: 1.3; margin-top: 24px; }
  .contact-list { list-style: none; margin-top: 8px; }
  .contact-list li {
    display: flex; align-items: center; gap: 8px;
    font-size: 17.5px; line-height: 27px;
  }
  .contact-list svg { width: 15px; height: 15px; flex: none; fill: var(--gold); }

  .tagline-rule {
    position: absolute; left: 0; right: 0; top: 406px;
    display: flex; align-items: center; gap: 6px;
  }
  .tagline-rule::before, .tagline-rule::after {
    content: ""; flex: 1; height: 2px; background: var(--gold);
  }
  .tagline { font-size: 17px; font-weight: 700; color: var(--navy); }

  .back-mark {
    position: absolute; left: 0; right: 0; top: 170px;
    text-align: center; color: #ffffff;
    font-weight: 600; font-size: 40px; line-height: 1.3; letter-spacing: 0.02em;
  }
</style>
</head>
<body>
<main class="canvas">

  <section class="card card-front" aria-label="Business card front">
    <div class="brand-mark">RV Bone &amp;<br>Vitality Center</div>
    <div class="divider"></div>

    <div class="details">
      <h1 class="doctor-name">Lydia Vance, <span class="credential">M.D.</span></h1>
      <p class="doctor-title">Board Certified Hand and<br>Upper Extremity Surgeon</p>
      <p class="address">38517 North Willowmere Ave<br>Palm Verde, FL 33094</p>
      <ul class="contact-list">
        <li>
          <svg viewBox="0 0 16 16" aria-hidden="true"><path d="M2 6c0-2 2-3 6-3s6 1 6 3v1h-3V6H5v1H2z"/><path d="M3 8h10l1 5H2z"/></svg>
          954-218-4063
        </li>
        <li>
          <svg viewBox="0 0 16 16" aria-hidden="true"><rect x="4" y="1" width="8" height="4"/><rect x="1" y="6" width="14" height="6" rx="1"/><rect x="4" y="10" width="8" height="5"/></svg>
          954-582-7341
        </li>
        <li>
          <svg viewBox="0 0 16 16" aria-hidden="true"><path d="M1 3h14v10H1z M1 3l7 6 7-6" /></svg>
          info@myrvbonecare.example
        </li>
      </ul>
    </div>

    <div class="tagline-rule"><span class="tagline">Grounded in Care. Built for You</span></div>
  </section>

  <section class="card card-back" aria-label="Business card back">
    <div class="back-mark">RV Bone &amp;<br>Vitality Center</div>
  </section>

</main>
</body>
</html>
```